Brightway Haus Inc. Business Card Design

Brightway Haus Inc. is in search of a great clean design for our business cards!

Looking to incorporate our full logo and watermark on side one (however, I am open to having the text and watermark separated within the design.)

On side two, I am looking to have contact information (Name, Position, Phone #, Email, Website (www.thebrightwayhaus.ca). Can have the logo and/or watermark as part of the design if applicable.

Please add tagline "Where Shine Counts" on either side 1 or 2. This tagline can be in a sans serif, serif or cursive font as long as it compliments overall design. Capitalization can be title or sentence case depending on how it fits within the design.

Get creative!! Looking for a clean, crisp, premium design! Looking for a glossy card finish with spot UV features when printed. Cards will also be printed with rounded corners. Standard dimensions (3.5 x 2).

Target Market(s)

B2B - primary clients are business owners or property management corporations. (residential jobs are few and far between)

Industry/Entity Type

Business

Contact Information for Business Card

- clean, crisp design
- double sided
- spot UV accents and glossy finish upon printing
- standard business card size (3.5 x 2) with rounded corners
- please see project description for requirements per side

Font styles to use
Sans Serif

Requirements
Must have
• - adequate bleeds with print ready files
• - cohesive design elements between side 1 & 2
• - spot UV elements (can be on both sides or just one, use your discretion)
• - colour pallet should match the logo file provided
• - incorporate tagline "where shine counts" (this tagline can be in a serif or sans serif font as long as it is complimentary to the overall design.
Nice to have
• - Premium elements with a clean design
Should not have
• - Please omit cartoon or whimsical like designs, think premium.
• - Colours should not stray from the pallet of the provided logo.

```html
<!DOCTYPE html>
<html lang="en">
<head>
<meta charset="utf-8">
<title>Brightway Haus Inc. Business Card</title>
<link rel="stylesheet" href="https://fonts.googleapis.com/css2?family=Open+Sans:wght@400;600;700;800&display=swap">
<style>
  :root {
    --navy: #1b2660;
    --navy-light: #3d4f95;
    --teal: #1fbfc0;
    --teal-light: #40d4d2;
    --ink: #3a3d45;
    --paper: #ffffff;
    --backdrop: #2a2b2e;
  }
  * { box-sizing: border-box; margin: 0; padding: 0; }
  html, body { width: 1200px; height: 834px; overflow: hidden; }
  body {
    background: var(--backdrop);
    font-family: "Open Sans", Arial, sans-serif;
    position: relative;
  }
  .card {
    position: absolute;
    width: 600px;
    height: 343px;
    border-radius: 14px;
    overflow: hidden;
    box-shadow: 0 14px 34px rgba(0,0,0,.45);
  }
  .card-front {
    left: 150px; top: 50px;
    background: radial-gradient(ellipse at 45% 40%, var(--navy-light) 0%, var(--navy) 62%);
  }
  .card-back { left: 450px; top: 440px; background: var(--paper); }
  .wave { position: absolute; inset: 0; }
  .brand {
    position: absolute;
    display: flex; align-items: center; gap: 12px;
    font-size: 28px; font-weight: 800; letter-spacing: .5px; white-space: nowrap;
  }
  .brand-mark { display: block; width: 28px; height: 28px; background: var(--teal); }
  .card-front .brand { left: 95px; top: 100px; color: var(--paper); }
  .card-back .brand { left: 70px; top: 70px; color: var(--navy); }
  .tagline {
    position: absolute; left: 360px; top: 250px;
    font-size: 15px; font-weight: 700; color: var(--navy);
    transform: rotate(-14deg); transform-origin: left center;
  }
  .person { position: absolute; left: 70px; top: 170px; }
  .person-name { font-size: 19px; font-weight: 700; color: var(--ink); }
  .person-role { font-size: 16px; font-weight: 400; color: var(--teal); margin-top: 2px; }
  .contact-list { position: absolute; left: 90px; top: 240px; list-style: none; }
  .contact-list li {
    display: flex; align-items: center; gap: 12px;
    font-size: 14px; color: var(--ink); height: 24px;
  }
  .contact-list svg { width: 16px; height: 16px; flex: none; }
</style>
</head>
<body>

<section class="card card-front" aria-label="Card front">
  <svg class="wave" viewBox="0 0 600 343" preserveAspectRatio="none" aria-hidden="true">
    <path d="M0 278 Q 330 250 600 128 L600 343 L0 343 Z" fill="#e8eef2"/>
    <path d="M0 290 Q 335 262 600 142 L600 343 L0 343 Z" fill="var(--teal)"/>
    <path d="M0 320 Q 335 292 600 180 L600 343 L0 343 Z" fill="var(--teal-light)" opacity=".45"/>
  </svg>
  <div class="brand"><span class="brand-mark"></span>BRIGHTWAY HAUS INC.</div>
  <p class="tagline">Where Shine Counts</p>
</section>

<section class="card card-back" aria-label="Card back">
  <div class="brand"><span class="brand-mark"></span>BRIGHTWAY HAUS INC.</div>
  <div class="person">
    <p class="person-name">Marc Delaney</p>
    <p class="person-role">President</p>
  </div>
  <ul class="contact-list">
    <li>
      <svg viewBox="0 0 16 16" fill="none" stroke="var(--teal)" stroke-width="1.4"><path d="M4 1.5 L6.5 4.5 L5 6.5 Q6.5 9.5 9.5 11 L11.5 9.5 L14.5 12 L12.5 14.5 Q5 13.5 1.5 4 Z"/></svg>
      905-555-0147
    </li>
    <li>
      <svg viewBox="0 0 16 16" fill="none" stroke="var(--teal)" stroke-width="1.4"><rect x="1.5" y="3.5" width="13" height="9"/><path d="M1.5 3.5 L8 9 L14.5 3.5"/></svg>
      info@thebrightwayhaus.ca
    </li>
    <li>
      <svg viewBox="0 0 16 16" fill="none" stroke="var(--teal)" stroke-width="1.3"><circle cx="8" cy="8" r="6.5"/><ellipse cx="8" cy="8" rx="3" ry="6.5"/><path d="M1.5 8 H14.5"/></svg>
      www.thebrightwayhaus.ca
    </li>
  </ul>
</section>

</body>
</html>
```